Norvane Website Design (New Start Up Investment Management Firm)

We need a website designed. We have attached a Powerpoint with our proposed website content (which is quite minimal), the format is just a suggestion but we would like to see your alternative and improved ideas. We are a boutique investment firm so are looking for something sleek and professional. I have included on the last page of the attachment our brand colours and font styles as well as attaching our logo design. We would like the successful designer to design the website and build the buttons etc.

On the "Contact Us" page, we are open to suggestions on how best to show the map, whether is should be static or open a google maps page. We would like the phone number and email address to be set up so people can click on them on their phone and it calls us or emails us directly.

We would prefer not to have photos of landscapes on the site.
Our website is hosted on a Linux based website.

We would also like 3 links at the bottom of each page for links to pdfs:
- Disclaimer, Terms and Conditions of Web Site Use
- Stewardship
- Pillar III

Target Market(s)

Institutional Investors

Industry/Entity Type

Investment

Coding

Coded - Design and coding required

Number of Pages Required

3 page

Font styles to use
Other font styles liked:
• Logo: Lato, Text: Source Sans Pro

Colors

Designer to choose colors to be used in the design.

Requirements
Must have
• The website must use the colours and fonts on the last page of the attached powerpoint. I can't see an option to select the exact colour palette below so please look at the PPT.
• For others please see Project description.
Should not have
• Landscape photos

```html
<!DOCTYPE html>
<html lang="en">
<head>
<meta charset="utf-8">
<title>Norvane Investment Management</title>
<link rel="stylesheet" href="https://fonts.googleapis.com/css2?family=Source+Sans+Pro:wght@400;600;700&display=swap">
<style>
  :root {
    --sky: #6bb1e6;
    --royal: #003ea6;
    --navy: #002f62;
    --lead-blue: #0a3ea6;
    --body-text: #4a4a4a;
    --footer-bg: #f8f8f8;
    --page-light: #f8f8f8;
    --page-shade: #ececec;
    --white: #ffffff;
    --footer-text: #3a3a3a;
  }
  * { margin: 0; padding: 0; box-sizing: border-box; }
  html, body { width: 1200px; height: 818px; overflow: hidden; }
  body {
    position: relative;
    background: var(--white);
    font-family: "Source Sans Pro", Arial, sans-serif;
  }
  .backdrop { position: absolute; inset: 0; width: 1200px; height: 818px; }
  .hero {
    position: absolute; left: 199px; top: 90px; width: 798px; height: 294px;
    background: var(--sky); color: var(--white); text-align: center;
  }
  .brand {
    position: absolute; left: 0; right: 0; top: 68px;
    display: flex; justify-content: center; align-items: center; gap: 14px;
  }
  .brand-square { width: 50px; height: 50px; background: var(--white); }
  .brand-name { font-size: 52px; font-weight: 600; letter-spacing: 1px; line-height: 1; }
  .hero-title {
    position: absolute; left: 0; right: 0; top: 176px;
    font-size: 30px; font-weight: 600; letter-spacing: 0.3px;
  }
  .side-nav { position: absolute; left: 199px; top: 424px; width: 252px; list-style: none; }
  .side-nav li {
    height: 74px; display: flex; align-items: center; padding-left: 21px;
    color: var(--white); font-size: 13px; font-weight: 700; letter-spacing: 0.2px;
  }
  .side-nav .is-active { background: var(--royal); }
  .side-nav .approach { background: var(--navy); }
  .side-nav .contact { background: var(--sky); }
  .about { position: absolute; left: 474px; top: 418px; width: 510px; }
  .about-heading { color: var(--navy); font-size: 18px; font-weight: 700; letter-spacing: 0.3px; }
  .about-rule { width: 26px; height: 2px; background: var(--navy); margin-top: 6px; }
  .about-lead {
    margin-top: 30px; color: var(--lead-blue); font-size: 18.5px; line-height: 22.5px;
  }
  .about-body {
    margin-top: 26px; color: var(--body-text); font-size: 13.3px; line-height: 22.5px;
  }
  .site-footer {
    position: absolute; left: 0; top: 736px; width: 1200px; height: 82px;
    background: var(--footer-bg);
  }
  .footer-brand {
    position: absolute; left: 209px; top: 31px; display: flex; align-items: center; gap: 7px;
    color: var(--royal); font-size: 14px; font-weight: 700;
  }
  .footer-square { width: 18px; height: 18px; background: var(--royal); }
  .footer-links {
    position: absolute; left: 300px; top: 34px; font-size: 11px; font-weight: 600; color: var(--footer-text);
  }
  .legal {
    position: absolute; right: 216px; top: 27px; text-align: right; font-size: 10.5px; color: var(--footer-text);
  }
  .legal-links { font-weight: 600; }
  .legal-copy { margin-top: 6px; }
  .page-code { position: absolute; right: 25px; top: 34px; font-size: 9.5px; color: #555; }
</style>
</head>
<body>
  <svg class="backdrop" viewBox="0 0 1366 931" preserveAspectRatio="none" aria-hidden="true">
    <polygon points="0,0 960,0 0,655" fill="var(--page-light)"/>
    <polygon points="860,0 1366,0 1366,460" fill="var(--page-shade)"/>
    <polygon points="960,0 1090,0 975,100" fill="#e4e4e4"/>
  </svg>

  <header class="hero">
    <div class="brand">
      <span class="brand-square"></span>
      <span class="brand-name">NORVANE</span>
    </div>
    <h1 class="hero-title">WE ARE A BOUTIQUE INVESTMENT FIRM</h1>
  </header>

  <ul class="side-nav">
    <li class="is-active">ABOUT&nbsp; NORVANE</li>
    <li class="approach">OUR APPROACH &amp; PHILOSOPHY</li>
    <li class="contact">CONTACT US</li>
  </ul>

  <main class="about">
    <h2 class="about-heading">ABOUT&nbsp; NORVANE</h2>
    <div class="about-rule"></div>
    <p class="about-lead">Norvane Investment Management was founded in 2016 with a clear vision to create an independent and nimble firm focused on generating superior risk-adjusted returns.</p>
    <p class="about-body">Norvane has designed an innovative investment approach which aims to harness the best elements of alternative investment management whilst reducing its recognised shortcomings. We are a performance and client focused firm, committed to building lasting relationships, treating our clients like partners rather than revenue streams.</p>
  </main>

  <footer class="site-footer">
    <div class="footer-brand"><span class="footer-square"></span></div>
    <div class="footer-links">Stewardship&nbsp; |&nbsp; Pillar III</div>
    <div class="legal">
      <div class="legal-links">Disclaimer&nbsp; | Terms and Conditions</div>
      <div class="legal-copy">© 2017 Company Name&nbsp; |&nbsp; All Rights Reserved</div>
    </div>
    <div class="page-code">C5</div>
  </footer>
</body>
</html>
```